Web Design Project

Psychotherapy and Counselling Practice needs a landing page web design.

My business "Larkfield Advisory" specialises in the treatment of Anxiety and Depression with a holistic approach, endeavouring to unlock the key that holds us to ransom in a life that is imbalanced, frustrating, and ultimately of our own making due to our own perceptions and behaviours.

There is much that impacts us which we cannot change, but we are always in control of how we think, and how we frame our experiences.....learning to challenge those thoughts and behaviours that are destructive and disempowering opens up a world of joyful possibility. Life is about making choices, learn to make wiser and healthier choices.......

Larkfield Advisory has a client base of individual clients but will seek to expand to offer services to the Corporate world by offering an adjunct to employers for established "Wellness Programs".

Larkfield Advisory is a highly professional, ethically bound business, with the needs of the client at the forefront of all we do.

Larkfield Advisory wishes to avoid the usual "jargon driven" psychobabble offered on many counselling web pages. It aims to be stylishly presented, clean in look and with as few "words" as possible and a largely white background (faster loading and more powerful impact of what is stated), those words contained in the webpage should be meaningful, persuasive and have an impact simply at glance. Larkfield does not want , or expect, those prospective clients in need of support , to be reading through volumes of industry driven cliches.

At this point Larkfield is just looking for a high quality landing page. However in time this will likely expand to include other sections such as case studies, video content etc.

Target Market(s)

Those in need of emotional support, suffering mental health issues, and those simply wanting to become self aware supported by a mindful therapist.

Industry/Entity Type

Industry

Requirements
Must have
• The design must incorporate the Larkfield logo and colour schemes found on the attached files.

```html
<!DOCTYPE html>
<html lang="en">
<head>
<meta charset="utf-8">
<title>Larkfield Advisory</title>
<link rel="stylesheet" href="https://fonts.googleapis.com/css2?family=Ubuntu:wght@300;400;500;700&display=swap">
<style>
  :root {
    --green: #8aab0a;
    --grey-dark: #6e6e6e;
    --grey-text: #9b9b9b;
    --grey-mid: #8a8a8a;
    --hero-bg: #f8f8f8;
    --panel: #ffffff;
    --white: #ffffff;
  }
  * { margin: 0; padding: 0; box-sizing: border-box; }
  html, body { width: 1200px; height: 1000px; overflow: hidden; background: var(--white); }
  body { position: relative; font-family: "Ubuntu", Arial, sans-serif; }

  .hero {
    position: absolute; left: 0; top: 222px; width: 1200px; height: 680px;
    background: var(--hero-bg);
  }
  .hero-panel {
    position: absolute; left: 612px; top: 90px; width: 546px; height: 440px;
    background: var(--panel);
  }

  .brand-box {
    position: absolute; left: 85px; top: 0; width: 300px; height: 248px;
    background: var(--grey-dark); border-top: 4px solid #8c8c8c;
  }
  .brand-box .brand-name {
    position: absolute; left: 0; right: 0; top: 102px; text-align: center;
    color: var(--white); font-weight: 300; font-size: 36px; letter-spacing: 1px;
  }
  .brand-box .tagline {
    position: absolute; left: 14px; top: 174px; width: 271px; height: 53px;
    background: var(--green); color: var(--white);
    font-weight: 700; font-size: 16px; line-height: 53px; text-align: center;
  }

  .main-nav { position: absolute; top: 176px; left: 0; width: 1200px; }
  .main-nav a {
    position: absolute; color: var(--green); text-decoration: none;
    font-weight: 500; font-size: 17px; letter-spacing: 0.3px;
  }

  .hero-wordmark {
    position: absolute; left: 82px; top: 528px;
    color: var(--green); font-weight: 300; font-size: 84px; letter-spacing: 2px;
  }

  .quote {
    position: absolute; left: 697px; top: 352px;
    color: var(--grey-text); font-weight: 500; font-size: 28px; line-height: 44px;
  }
  .quote .line2 { padding-left: 18px; display: block; }
  .quote-source {
    position: absolute; left: 715px; top: 444px;
    color: var(--grey-mid); font-weight: 500; font-size: 16px;
  }
  .statement {
    position: absolute; left: 715px; top: 564px;
    color: var(--grey-text); font-weight: 500; font-size: 21px;
  }
  .statement .accent { color: var(--green); }
  .contact { position: absolute; left: 715px; top: 632px; color: var(--grey-text); font-weight: 500; }
  .contact .name { font-size: 22px; }
  .contact .credentials { font-size: 16px; margin-top: 6px; }
  .contact .details { font-size: 16px; margin-top: 30px; line-height: 26px; }

  .ground { position: absolute; left: 0; top: 770px; width: 1200px; height: 132px; }

  .site-footer .copyright {
    position: absolute; left: 83px; top: 937px;
    color: var(--grey-dark); font-weight: 700; font-size: 12px;
  }
  .site-footer .social {
    position: absolute; top: 927px; width: 30px; height: 29px; background: var(--green);
  }
  .site-footer .web {
    position: absolute; right: 98px; top: 933px;
    color: var(--grey-dark); font-weight: 500; font-size: 17px;
  }
  .site-footer .web .accent { color: var(--green); }
</style>
</head>
<body>
  <div class="hero">
    <div class="hero-panel"></div>
  </div>

  <header>
    <div class="brand-box">
      <div class="brand-name">LARKFIELD</div>
      <div class="tagline">Advisory is what you may need</div>
    </div>
    <nav class="main-nav">
      <a href="#" style="left:635px">HOME</a>
      <a href="#" style="left:715px">ABOUT US</a>
      <a href="#" style="left:833px">CONTACT US</a>
      <a href="#" style="left:994px">CASE STUDIES</a>
    </nav>
  </header>

  <main>
    <div class="hero-wordmark">LARKFIELD</div>

    <p class="quote">“With the new day comes<span class="line2">new strength new thoughts.”</span></p>
    <p class="quote-source">( Helen Marsh )</p>

    <p class="statement"><span class="accent">Advisory</span> is highly Professional</p>

    <div class="contact">
      <div class="name">MEL HARROW</div>
      <div class="credentials">BA (Psych) BSc (Hons) Psych MBPS</div>
      <div class="details">Mobile: 0400 318 562<br>E-mail: mel.harrow@mailpost.net</div>
    </div>

    <svg class="ground" viewBox="0 0 1200 132" aria-hidden="true">
      <path d="M0 50 C 300 70, 700 55, 1200 40 L1200 132 L0 132 Z" fill="#707070"/>
      <path d="M0 28 C 250 55, 600 45, 1080 26 C 700 40, 300 62, 0 50 Z" fill="#8aab0a"/>
      <path d="M0 52 C 300 72, 700 57, 1200 42 L1200 48 C 700 62, 300 78, 0 60 Z" fill="#ffffff"/>
    </svg>
  </main>

  <footer class="site-footer">
    <p class="copyright">© Copyright Larkfield 2013 . Alright reserve</p>
    <span class="social" style="left:406px" aria-label="Social link"></span>
    <span class="social" style="left:447px" aria-label="Social link"></span>
    <p class="web">www.<span class="accent">larkfieldadvisory</span>.com.au</p>
  </footer>
</body>
</html>
```